Professional & attention grabbing.

A business card design, front and back. I already have a logo I will attach, but I am open to something new as well.
Things to include:
Name:
Title:
Phone:
Email:
Wanting something that is professional but attention grabbing.
Also we do a lot of work using drones on natural gas pipelines (leading the future)if you want to include any of that. I'm open to ideas.
Target Market(s)
Natural gas transmission industry / greenhouse gas mitigation industry
Industry/Entity Type
Business
Colors
Designer to choose colors to be used in the design.
Look and feel
Each slider illustrates characteristics of the customer's brand and the style your logo design should communicate.

```html
<!DOCTYPE html>
<html lang="en">
<head>
<meta charset="utf-8">
<title>Kestrel Line Inspections – Business Card</title>
<link rel="stylesheet" href="https://fonts.googleapis.com/css2?family=Open+Sans:ital,wght@0,400;0,600;1,400&display=swap">
<style>
  :root {
    --brand-red: #c01f25;
    --ink-dark: #3a3a3c;
    --ink-body: #444446;
    --card-white: #ffffff;
    --backdrop: #e4e4e4;
  }
  * { margin: 0; padding: 0; box-sizing: border-box; }
  html, body {
    width: 1200px;
    height: 987px;
    overflow: hidden;
  }
  body {
    position: relative;
    background: var(--backdrop);
    font-family: "Open Sans", Arial, sans-serif;
  }
  .card {
    position: absolute;
    left: 293px;
    width: 615px;
    height: 351px;
  }
  .card--front { top: 130px; background: var(--card-white); }
  .card--back  { top: 505px; background: var(--brand-red); }

  /* Front: wordmark */
  .wordmark {
    position: absolute;
    right: 38px;
    top: 188px;
    transform: translateY(-100%);
    display: flex;
    align-items: center;
    gap: 12px;
  }
  .wordmark__square {
    width: 40px;
    height: 40px;
    background: var(--brand-red);
  }
  .wordmark__name {
    font-weight: 600;
    font-size: 21px;
    color: var(--ink-dark);
    letter-spacing: 0.2px;
  }
  .card--front .wordmark { top: 100px; transform: none; }

  /* Front: identity */
  .accent-bar {
    position: absolute;
    left: 0;
    top: 198px;
    width: 13px;
    height: 42px;
    background: var(--brand-red);
  }
  .identity {
    position: absolute;
    left: 47px;
    top: 192px;
  }
  .identity__name {
    font-weight: 600;
    font-size: 22px;
    line-height: 1.2;
    color: var(--brand-red);
    text-transform: uppercase;
  }
  .identity__title {
    font-size: 17px;
    line-height: 1.3;
    color: var(--ink-body);
    text-transform: uppercase;
  }
  .contacts {
    position: absolute;
    left: 47px;
    top: 250px;
    list-style: none;
  }
  .contacts__item {
    display: flex;
    align-items: center;
    gap: 8px;
    font-size: 16px;
    line-height: 23.5px;
    color: var(--ink-body);
  }
  .contacts__icon {
    width: 14px;
    height: 14px;
    fill: var(--brand-red);
    flex: none;
  }

  /* Back */
  .back-mark {
    position: absolute;
    left: 443px;
    top: 184px;
    width: 120px;
    height: 120px;
    background: var(--card-white);
  }
  .back-url {
    position: absolute;
    right: 38px;
    top: 311px;
    font-style: italic;
    font-size: 16px;
    color: var(--card-white);
  }
</style>
</head>
<body>

<section class="card card--front" aria-label="Business card front">
  <div class="wordmark">
    <span class="wordmark__square"></span>
    <span class="wordmark__name">Kestrel Line Inspections</span>
  </div>

  <span class="accent-bar"></span>
  <div class="identity">
    <p class="identity__name">Daniel Reyes</p>
    <p class="identity__title">CEO/Founder</p>
  </div>

  <ul class="contacts">
    <li class="contacts__item">
      <svg class="contacts__icon" viewBox="0 0 24 24" aria-hidden="true"><path d="M6.6 10.8a15.1 15.1 0 0 0 6.6 6.6l2.2-2.2c.3-.3.7-.4 1-.2 1.1.4 2.3.6 3.6.6.6 0 1 .4 1 1V20c0 .6-.4 1-1 1A17 17 0 0 1 3 4c0-.6.4-1 1-1h3.5c.6 0 1 .4 1 1 0 1.3.2 2.5.6 3.6.1.3 0 .7-.2 1z"/></svg>
      555 210 4876
    </li>
    <li class="contacts__item">
      <svg class="contacts__icon" viewBox="0 0 24 24" aria-hidden="true"><path d="M2 5h20v14H2z M2 5l10 8 10-8" fill-rule="evenodd"/><path d="M3 6.5l9 7 9-7V5H3z" fill="#fff"/></svg>
      daniel@kestrelinspect.com
    </li>
    <li class="contacts__item">
      <svg class="contacts__icon" viewBox="0 0 24 24" aria-hidden="true"><circle cx="12" cy="12" r="10"/><path d="M2 12h20M12 2c3 3 3 17 0 20M12 2c-3 3-3 17 0 20" stroke="#fff" stroke-width="1.6" fill="none"/></svg>
      www.kestrelinspect.com
    </li>
  </ul>
</section>

<section class="card card--back" aria-label="Business card back">
  <span class="back-mark"></span>
  <p class="back-url">www.kestrelinspect.com</p>
</section>

</body>
</html>
```